Graphic Design Project

ok I have the artwork for my presentation folder, and I have the text to put on the folder, I need you to apply text to the folder and the single sheets, so inside the artwork is pictures to use, text to use. thank you so much ask me as many questions as you need
Updates

my girl forgot to upload the mock ups of the presentation folder and single sheets, my apologies please check updated files

Hey Guys this is a eazy project the artwork is done, the text is done, the pictures are done!, all you have to do is assemble the project, I even have mock up pictures of how project looks finished, I have made the money good so that you would not pass on this project because it is not that creative of a job!

Target Market(s)

Dr's and patients

Industry/Entity Type

Graphic Design

Requirements
Must have
• use the single sheet artwork to make as many single sheets as you need to use all of the text supplied
Should not have
• do not make this, so professional looking that it does not appeal to the patients

```html
<!DOCTYPE html>
<html lang="en">
<head>
<meta charset="utf-8">
<title>BrightPath Counseling – Services Sheet</title>
<link rel="stylesheet" href="https://fonts.googleapis.com/css2?family=Arimo:ital,wght@0,400;0,700;1,400&display=swap">
<style>
  :root {
    --grey-band: #c9c9cc;
    --beige-band: #d5cdbd;
    --white: #ffffff;
    --panel: #f3f3f3;
    --ink: #2a2a2a;
    --photo-top: #7f9a5c;
    --photo-bottom: #4f6a3b;
  }
  html, body {
    margin: 0;
    padding: 0;
    overflow: hidden;
    background: var(--white);
  }
  .sheet {
    position: relative;
    width: 932px;
    height: 1200px;
    overflow: hidden;
    font-family: "Arimo", Arial, sans-serif;
    color: var(--ink);
  }
  .backdrop {
    position: absolute;
    inset: 0;
  }
  .content-panel {
    position: absolute;
    left: 49px;
    top: 53px;
    width: 839px;
    height: 1097px;
    background: var(--panel);
    border-radius: 18px;
  }
  .services {
    position: absolute;
    left: 83px;
    top: 96px;
    width: 790px;
  }
  .services-title {
    margin: 0 0 14px;
    font-size: 17px;
    font-weight: 700;
    letter-spacing: 0.2px;
  }
  .services-list {
    list-style: none;
    margin: 0;
    padding: 0;
    font-size: 17px;
    font-style: italic;
    line-height: 33px;
  }
  .photo-frame {
    position: absolute;
    left: 138px;
    top: 349px;
    width: 677px;
    height: 456px;
    background: var(--white);
  }
  .photo-area {
    position: absolute;
    left: 9px;
    top: 9px;
    right: 9px;
    bottom: 9px;
    background: linear-gradient(180deg, var(--photo-top), #98a77a 45%, var(--photo-bottom));
  }
  .intro {
    position: absolute;
    left: 83px;
    top: 828px;
    width: 770px;
    font-size: 19.5px;
    line-height: 29px;
  }
  .intro p {
    margin: 0 0 24px;
  }
</style>
</head>
<body>
<div class="sheet">
  <svg class="backdrop" width="932" height="1200" viewBox="0 0 932 1200" aria-hidden="true">
    <rect width="932" height="1200" fill="var(--white)"/>
    <polygon points="0,0 932,0 932,700 0,760" fill="var(--grey-band)"/>
    <polygon points="0,700 932,640 932,1200 0,1200" fill="var(--beige-band)"/>
    <polygon points="700,0 760,0 932,30 932,60" fill="var(--white)"/>
    <polygon points="0,690 420,760 420,790 0,720" fill="var(--white)"/>
    <polygon points="880,520 932,430 932,470 890,560" fill="var(--white)"/>
    <polygon points="800,1200 932,950 932,1000 830,1200" fill="var(--white)"/>
  </svg>

  <div class="content-panel"></div>

  <section class="services">
    <h2 class="services-title">SERVICES PROVIDED:</h2>
    <ul class="services-list">
      <li>- Pro-Active Opioid Education</li>
      <li>- Screening for potential substance use disorders related to prescribed and non-prescribed</li>
      <li>- Educating patients about the risks, warnings, and symptoms of over the counter medications</li>
      <li>- Educational materials given to patients about the risk of taking medications inappropriately</li>
      <li>- Assessment for substance use disorders related to medical issues and prescribed medications</li>
      <li>- Counseling provided by highly trained, competent and experienced professionals.</li>
    </ul>
  </section>

  <div class="photo-frame">
    <div class="photo-area" role="img" aria-label="Photo of four smiling young friends posing together outdoors beside a tree"></div>
  </div>

  <section class="intro">
    <p>BrightPath Counseling is dedicated to providing an unprecedented level of information, resources and educational support to your patients. We are committed to promoting a culture of transparency, documentation for doctors, meaningful interaction and active participation that will allow patients to assume a greater role in their healthcare through pro active addiction education, assessment, prevention, and screening.</p>
    <p>Good patient education can be invaluable to both physician and patient. A patient who is educated about his or her health issues is far better prepared to work with their physician as a partner in managing their pain. Those patients are also more likely to have an internal locus - not expecting the doctor to "fix" everything, but relying on themselves as well. Understanding their medications equals better compliance.</p>
  </section>
</div>
</body>
</html>
```